Business Card Design Project

We are not a new company, but renamed to "Vantorin Kitchens" last year. We specialize in modern high-end cabinetry imports. We would like to communicate a sense of quality and cutting edge technology. Ideally the design would incorporate our logo colors, silver, red and preferably a black, matte background. Though we are open to suggestions.
Logo is attached.
Edit: I have attached rough drafts of the previous cards, this way you will have all necessary content that needs to go on the cards.
Updates
Project Deadline Extended
Reason: We have received a lot of great designs, but due to the sheer number we couldn't respond to all. We will extend the deadline for another 7 days to finalize and provide feedback to designers.
Thank you for your hard work!
Industry/Entity Type
Business
Look and feel
Each slider illustrates characteristics of the customer's brand and the style your logo design should communicate.

```html
<!DOCTYPE html>
<html lang="en">
<head>
<meta charset="utf-8">
<title>Vantorin Kitchens – Business Cards</title>
<link href="https://fonts.googleapis.com/css2?family=Arimo:wght@400;700&family=Source+Sans+3:wght@400&display=swap" rel="stylesheet">
<style>
  :root {
    --stage: #c9a47c;
    --card-top: #2b2b2b;
    --card-bottom: #0f0f0f;
    --silver: #c9c9c9;
    --silver-light: #e4e4e4;
    --silver-dark: #8d8d8d;
    --red: #e3202a;
    --white: #ffffff;
    --label: #1a1208;
  }
  * { margin: 0; padding: 0; box-sizing: border-box; }
  html, body { width: 1200px; height: 788px; overflow: hidden; }
  body {
    position: relative;
    background: var(--stage);
    font-family: "Arimo", Arial, sans-serif;
  }
  .sheet-label {
    position: absolute;
    font-family: "Source Sans 3", "Myriad Pro", sans-serif;
    font-size: 22px;
    color: var(--label);
    transform: translateX(-50%);
  }
  .card {
    position: absolute;
    width: 525px;
    height: 300px;
    border-radius: 20px;
    overflow: hidden;
    background: linear-gradient(180deg, var(--card-top), var(--card-bottom));
    box-shadow: 0 4px 10px rgba(0,0,0,.35);
  }
  .card--front   { left: 53px;  top: 70px; }
  .card--front-1 { left: 622px; top: 70px; }
  .card--back    { left: 56px;  top: 446px; }
  .card--back-1  { left: 624px; top: 446px; background: #080808; }

  .brand-name {
    position: absolute;
    color: var(--silver);
    font-weight: 700;
    text-transform: uppercase;
    white-space: nowrap;
    transform: translateX(-50%);
  }
  .card--front .brand-name,
  .card--front-1 .brand-name { left: 169px; top: 98px; font-size: 19px; letter-spacing: 1px; }
  .card--back .brand-name,
  .card--back-1 .brand-name { left: 262px; top: 160px; font-size: 28px; letter-spacing: 2px; }
  .card--back-1 .brand-name { left: 270px; top: 170px; }

  .contact {
    position: absolute;
    left: 331px;
    top: 50px;
    color: var(--white);
    font-size: 14px;
    line-height: 1;
  }
  .card--front-1 .contact { left: 318px; }
  .contact__name { font-size: 17px; font-weight: 700; margin-bottom: 6px; }
  .card--front-1 .contact__name { font-weight: 400; }
  .contact__role { font-size: 16px; margin-bottom: 16px; }
  .card--front-1 .contact__role { font-size: 14px; }
  .contact__line { margin-bottom: 7px; }
  .contact__line b { font-weight: 700; }
  .contact__email { margin-top: 14px; }

  .swoosh { position: absolute; left: 0; top: 0; width: 525px; height: 300px; }
  .address {
    position: absolute;
    left: 30px;
    top: 247px;
    color: var(--white);
    font-size: 13.5px;
    line-height: 19px;
  }

  .texture {
    position: absolute;
    background: radial-gradient(ellipse at center, #5a5a5a 0%, #2a2a2a 45%, rgba(8,8,8,0) 75%);
  }
  .texture--top { left: -20px; top: -30px; width: 320px; height: 140px; }
  .texture--bottom { left: 260px; top: 190px; width: 300px; height: 140px; }
</style>
</head>
<body>

  <div class="sheet-label" style="left:307px; top:22px;">front</div>
  <div class="sheet-label" style="left:888px; top:22px;">front-1</div>
  <div class="sheet-label" style="left:314px; top:405px;">back</div>
  <div class="sheet-label" style="left:885px; top:405px;">Back - 1</div>

  <section class="card card--front">
    <div class="brand-name">Vantorin Kitchens</div>
    <div class="contact">
      <div class="contact__name">DMITRI VARSK</div>
      <div class="contact__role">President</div>
      <div class="contact__line"><b>phone</b> : 555.201.0144</div>
      <div class="contact__line"><b>cell</b> : 555.201.3872</div>
      <div class="contact__line"><b>fax</b> : 555.201.0190</div>
      <div class="contact__email">dmitri@vantorinkitchens.ca</div>
    </div>
    <svg class="swoosh" viewBox="0 0 525 300" aria-hidden="true">
      <defs>
        <linearGradient id="greyBand" x1="0" y1="0" x2="1" y2="0">
          <stop offset="0" stop-color="#b9b9b9"/>
          <stop offset="1" stop-color="#8a8a8a"/>
        </linearGradient>
      </defs>
      <path d="M0 208 C120 200 300 225 525 296 L525 300 L0 300 Z" fill="url(#greyBand)"/>
      <path d="M170 222 C320 232 440 262 525 262 L525 274 C430 276 320 246 170 222 Z" fill="#5e5e5e"/>
      <path d="M160 220 C330 236 440 250 525 226 L525 244 C440 266 330 248 160 220 Z" fill="var(--red)"/>
      <path d="M260 258 C380 280 460 290 525 272 L525 284 C460 300 380 290 260 258 Z" fill="#101010"/>
    </svg>
    <div class="address">2816 - 47 St.<br>Northgate, AB T0X 2K4</div>
  </section>

  <section class="card card--front-1">
    <div class="brand-name">Vantorin Kitchens</div>
    <div class="contact">
      <div class="contact__name">NIKOLAI VARSK</div>
      <div class="contact__role">Director</div>
      <div class="contact__line"><b>phone</b> : 555.201.0144</div>
      <div class="contact__line"><b>cell</b> : 555.201.6627</div>
      <div class="contact__line"><b>fax</b> : 555.201.0190</div>
      <div class="contact__email">nikolai@vantorinkitchens.ca</div>
    </div>
    <svg class="swoosh" viewBox="0 0 525 300" aria-hidden="true">
      <path d="M0 208 C120 200 300 225 525 296 L525 300 L0 300 Z" fill="url(#greyBand)"/>
      <path d="M170 222 C320 232 440 262 525 262 L525 274 C430 276 320 246 170 222 Z" fill="#5e5e5e"/>
      <path d="M160 220 C330 236 440 250 525 226 L525 244 C440 266 330 248 160 220 Z" fill="var(--red)"/>
      <path d="M260 258 C380 280 460 290 525 272 L525 284 C460 300 380 290 260 258 Z" fill="#101010"/>
    </svg>
    <div class="address">2816 - 47 St.<br>Northgate, AB T0X 2K4</div>
  </section>

  <section class="card card--back">
    <div class="brand-name">Vantorin Kitchens</div>
  </section>

  <section class="card card--back-1">
    <div class="texture texture--top" role="img" aria-label="Perforated metal texture, top left corner"></div>
    <div class="texture texture--bottom" role="img" aria-label="Perforated metal texture, bottom right corner"></div>
    <div class="brand-name">Vantorin Kitchens</div>
  </section>

</body>
</html>
```